Theatrical Producer/Consultant needs Artistic Brochure Shell and Inserts

Lanternfield Stageworks (www.lanternfieldstageworks.com) is a small company that offers theatrical producing and consulting services. We would like to create a brochure that contains information about our various productions and services. Because our roster is fluid, we are proposing to create a brochure shell or folder with pockets, and then a template for individual tear sheets that would be inserted into the inside pockets of the brochure shell/folder. The shell is intended for reuse each season, and new tear sheets will be developed separately on a project by project basis.
This task is to create the shell and a corresponding tear sheet template.
The brochure will be delivered by hand as well as by mail, so should fit into a standard size mailing envelope (i.e., within NPDS flat dimensions of 6 1/8" x 11 1/2")
The final design should reflect the high level of artistry of our theatrical projects. Attached are our logo as well as photos of current theatrical offerings which are available for use on the brochure shell but not required. There is also a file that describes our services in more detail, fyi. This will ultimately go onto one of the tear sheets in the brochure.
For the tear sheet template, we have also included a sample brochure from a peer colleague, just to give you an idea of the kind of information each sheet would contain. Each project page will contain title of the project, information about the artists involved, one or more photos, a project description, schedule, fee and other technical information.
The final files for both the shell and tear sheet templates should be printer-ready and also in a file format that we can edit ourselves in future.
Updates
Project Deadline Extended Reason: There was a discrepancy between posted project deadline (December 7) and when project was automatically closed (December 6). Since several designers who have not yet submitted indicated they were planning to submit designs, we wanted to make sure that they were able to do so. Added Monday, December 7, 2015
Industry/Entity Type
Performing Art
Font styles to use
Look and feel
Each slider illustrates characteristics of the customer's brand and the style your logo design should communicate.

```html
<!DOCTYPE html>
<html lang="en">
<head>
<meta charset="utf-8">
<title>Lanternfield Stageworks – Folder Shell</title>
<link rel="stylesheet" href="https://fonts.googleapis.com/css2?family=Lato:ital,wght@0,300;0,400;0,700;1,400&display=swap">
<style>
  :root{
    --stage:#3a3a3a;
    --paper:#ffffff;
    --teal:#14a3b8;
    --teal-deep:#0c8fa3;
    --ink:#3b3b3b;
    --flap-grey:#cfcfcf;
    --cutout:#2f2f2f;
  }
  *{margin:0;padding:0;box-sizing:border-box}
  html,body{width:802px;height:1200px;overflow:hidden}
  body{background:var(--stage);position:relative;font-family:"Lato",sans-serif;color:var(--ink)}
  .sheet{position:absolute;inset:0}
  .abs{position:absolute}

  /* outer cover */
  .cover{left:82px;top:44px;width:646px;height:484px;overflow:hidden;
    background:linear-gradient(180deg,#ffffff 0%,#eef8fa 22%,#bfe6ec 50%,#4fbccd 78%,var(--teal) 100%)}
  .cover-glow{left:270px;top:20px;width:376px;height:400px;border-radius:50%;
    background:radial-gradient(circle at 52% 50%,rgba(20,163,184,.28) 0%,rgba(20,163,184,.12) 45%,rgba(20,163,184,0) 70%)}
  .cover-haze{left:40px;top:70px;width:230px;height:230px;border-radius:50%;
    background:radial-gradient(circle,rgba(255,255,255,.35) 0%,rgba(255,255,255,0) 70%)}
  .cutout{left:380px;top:133px;width:176px;height:176px;border-radius:50%;background:var(--cutout);
    display:flex;align-items:center;justify-content:center;color:#fff;font-size:11px;letter-spacing:.5px}
  .wordmark{font-weight:400;line-height:1;white-space:nowrap;display:flex;align-items:center;gap:8px}
  .wordmark .dot{width:14px;height:14px;border-radius:50%;border:3px solid currentColor;flex:none}
  .wordmark--cover{left:339px;top:54px;font-size:25px;color:var(--teal-deep)}
  .wordmark--return{left:30px;top:346px;font-size:21px;color:#fff}
  .return-address{left:34px;top:393px;color:#fff;font-size:11.5px;line-height:17.6px;font-style:normal}
  .tagline{left:339px;top:360px;width:290px;color:#fff;font-weight:300;font-size:24px;line-height:30px}
  .tagline b{font-weight:700}

  /* inside spread */
  .inside{left:84px;top:620px;width:644px;height:482px;overflow:hidden;
    background:linear-gradient(180deg,#ffffff 0%,#ffffff 57%,#d3eef2 65%,#58c0cf 80%,var(--teal) 100%)}
  .inside-glow{left:300px;top:250px;width:420px;height:300px;border-radius:50%;
    background:radial-gradient(circle,rgba(12,143,163,.3) 0%,rgba(12,143,163,0) 70%)}
  .photo{border-radius:50%;border:2px solid var(--teal)}
  .photo--bright{border:4px solid #fff}
  .title{color:var(--teal);font-weight:400;font-size:17px;line-height:20px}
  .title small{font-size:14px}
  .copy{font-size:7.4px;line-height:11.4px}
  .copy .lead{color:var(--teal);font-size:16px;line-height:16px}
  .copy--italic{font-style:italic}
  .copy--accent{color:var(--teal);font-style:italic}
  .copy--light{color:#fff}
  .copy--light .lead{color:#fff}
  .url{font-size:7.4px;color:#fff}
</style>
</head>
<body>
<div class="sheet">

  <!-- cover pocket flap and side tab -->
  <svg class="abs" style="left:0;top:0" width="802" height="600" aria-hidden="true">
    <polygon points="82,528 404,528 392,576 82,576" fill="var(--teal)"/>
    <polygon points="82,484 82,532 46,524 46,492" fill="var(--teal)"/>
  </svg>

  <section class="abs cover">
    <div class="abs cover-haze" role="img" aria-label="Soft decorative backdrop"></div>
    <div class="abs cover-glow" role="img" aria-label="Soft decorative backdrop around the window"></div>
    <div class="abs cutout">Cutout</div>
    <div class="abs wordmark wordmark--cover"><span class="dot"></span>Lanternfield Stageworks</div>
    <div class="abs wordmark wordmark--return">Lanternfield Stageworks</div>
    <address class="abs return-address">Lanternfield Stageworks<br>48 Wrenfield Lane<br>Marlow Springs, NJ 08911</address>
    <p class="abs tagline">Dedicated to <b>producing and consulting</b> in the performing arts</p>
  </section>

  <!-- inside pocket and tab -->
  <svg class="abs" style="left:0;top:1040px" width="802" height="160" aria-hidden="true">
    <polygon points="408,62 728,62 728,112 416,112 420,86" fill="var(--flap-grey)"/>
    <polygon points="728,14 764,22 764,48 728,54" fill="var(--flap-grey)"/>
  </svg>

  <section class="abs inside">
    <div class="abs inside-glow" role="img" aria-label="Soft decorative backdrop"></div>

    <div class="abs photo" style="left:23px;top:42px;width:122px;height:122px;background:radial-gradient(circle at 55% 45%,#3d4a56,#0e1216 70%)" role="img" aria-label="Stage photo: hooded puppet figure under a spotlight"></div>
    <h2 class="abs title" style="left:156px;top:34px;width:150px">Lanternfield Stageworks <small>LLC</small></h2>
    <p class="abs copy" style="left:156px;top:78px;width:153px">is a company dedicated to producing and consulting in the performing arts. From experimental to commercial, we collaborate with artists and organizations to foster an expansive range of compelling theatrical works for local, national and international audiences. We eschew boundaries—aesthetic, geopolitical, institutional—and thrive on a nimble and rigorous practice.</p>

    <p class="abs copy" style="left:25px;top:208px;width:134px">As <span class="lead">producers</span> we generate and develop our own innovative theatrical projects, serve as a creative producer for hire (by producing companies, independent artists and others) and provide other creative project-based services, including program development and dramaturgy.</p>
    <div class="abs photo" style="left:173px;top:206px;width:122px;height:122px;background:radial-gradient(circle at 50% 30%,#8a8f86,#2d3a2a 45%,#08090a 75%)" role="img" aria-label="Stage photo: moonlit forest scene with performers"></div>

    <div class="abs photo" style="left:33px;top:342px;width:122px;height:122px;background:radial-gradient(circle at 50% 55%,#8b6e55,#2a1f18 70%)" role="img" aria-label="Stage photo: ensemble of animal puppets"></div>
    <p class="abs copy copy--light" style="left:171px;top:360px;width:146px">As <span class="lead">consultants</span> we work with theater companies, presenters, performing arts centers, foundations and other non-profit or commercial entities to provide ongoing programming advice, research and development as well as broad policy, leadership and structural input and oversight</p>

    <div class="abs photo" style="left:347px;top:24px;width:120px;height:120px;background:radial-gradient(circle at 50% 50%,#6a6e70,#1e2326 72%)" role="img" aria-label="Stage photo: two actors in a close dramatic scene"></div>
    <p class="abs copy" style="left:486px;top:30px;width:142px">Our model of producing and consulting varies project-by-project, organization-by-organization. Our projects reflect a broad spectrum of genre, scale and clients. We examine the individual elements and/or artists involved and shape producing strategy around their particular visions.</p>
    <p class="abs copy" style="left:486px;top:130px;width:142px">By customizing an approach that capitalizes on the strengths of</p>
    <p class="abs copy" style="left:336px;top:153px;width:292px">everyone involved and then identifying how to supplement those strengths we facilitate artistic excellence, while having a good time.</p>
    <p class="abs copy copy--accent" style="left:336px;top:190px;width:294px">At its core, Lanternfield Stageworks combines artistic values with an independent flexibility and financial structure that allow us to create a body of work that wouldn't exist under any other auspice.</p>

    <h2 class="abs title" style="left:336px;top:244px;width:130px">Lanternfield Stageworks <small>LLC</small></h2>
    <p class="abs copy copy--italic" style="left:336px;top:290px;width:125px">strives to be nimble, adaptive and clever, all qualities we share with the noble lantern.</p>
    <p class="abs url" style="left:338px;top:340px">www.lanternfieldstageworks.com</p>
    <div class="abs photo photo--bright" style="left:471px;top:226px;width:143px;height:143px;background:radial-gradient(circle at 50% 45%,#4a4f53,#0d0f11 72%)" role="img" aria-label="Stage photo: projected text on a darkened stage"></div>
  </section>

</div>
</body>
</html>
```